Hvac and insulation company needs good looking business card design

We are hvac and insulation company and looking for a new business cards that look to today standards designs

Target Market(s)

homeowners

Industry/Entity Type

Hvac

Contact Information for Business Card

Name: Walter Brinoku
Home comfort consultant
address: 4827 Dunmore St #215 Oakland, CA 94619
office: 888-316-2790
cell: 510-742-3185
Lic.# 584261
Email: walter@corvane-hvac.com
Web: corvane-hvac.com

Requirements
Must have
• clean and sleek look
Nice to have
• simple with a clean look
Should not have
• to busy business card

```html
<!DOCTYPE html>
<html lang="en">
<head>
<meta charset="UTF-8">
<title>Corvane Home Solutions — Business Card</title>
<link rel="stylesheet" href="https://fonts.googleapis.com/css2?family=Open+Sans:wght@400;600&display=swap">
<style>
  :root {
    --orange: #e8791c;
    --orange-line: #f08a24;
    --ink: #4a4a4a;
    --muted: #7a7a7a;
    --card-white: #ffffff;
    --card-grey-1: #6a6b6b;
    --card-grey-2: #555656;
    --backdrop: #d9dadb;
  }
  * { box-sizing: border-box; margin: 0; padding: 0; }
  html, body {
    width: 1200px; height: 900px; overflow: hidden;
    background: var(--backdrop);
    font-family: "Open Sans", sans-serif;
  }
  .sheet {
    width: 1200px; height: 900px;
    display: flex; flex-direction: column; align-items: center; justify-content: center;
    gap: 40px;
  }
  .card {
    width: 700px; height: 400px;
    border-radius: 22px;
    position: relative;
    box-shadow: 0 10px 28px rgba(0,0,0,.18);
    overflow: hidden;
  }
  .card--front { background: var(--card-white); }
  .card--back { background: linear-gradient(135deg, var(--card-grey-1), var(--card-grey-2)); }

  .brand { position: absolute; display: flex; align-items: center; gap: 12px; }
  .brand__mark { background: var(--orange); border-radius: 4px; }
  .brand__name { color: var(--orange); font-weight: 600; letter-spacing: -0.5px; line-height: 1; }
  .brand__tagline { position: absolute; color: var(--muted); letter-spacing: 4px; font-weight: 400; white-space: nowrap; }

  .card--front .brand { left: 56px; top: 52px; }
  .card--front .brand__mark { width: 40px; height: 40px; }
  .card--front .brand__name { font-size: 52px; }
  .card--front .brand__tagline { left: 110px; top: 114px; font-size: 15px; }

  .divider {
    position: absolute; left: 46px; top: 200px;
    width: 560px; height: 2px; background: var(--orange-line);
  }

  .contacts { position: absolute; left: 56px; top: 222px; list-style: none; }
  .contacts li {
    display: flex; align-items: center; gap: 12px;
    font-size: 17px; color: var(--ink); line-height: 32px; white-space: nowrap;
  }
  .contacts svg { width: 14px; height: 14px; fill: var(--orange); flex: none; }
  .contacts .accent { color: var(--orange); }

  .person { position: absolute; right: 52px; top: 52px; text-align: right; }
  .person__name { color: var(--orange); font-size: 26px; font-weight: 400; text-transform: uppercase; letter-spacing: .5px; line-height: 34px; white-space: nowrap; }
  .person__role { color: var(--ink); font-size: 17px; line-height: 24px; margin-top: 2px; }
  .person__address { color: var(--ink); font-size: 16px; line-height: 24px; margin-top: 8px; }

  .card--back .brand { left: 50%; top: 120px; transform: translateX(-50%); }
  .card--back .brand__mark { width: 64px; height: 64px; }
  .card--back .brand__name { font-size: 96px; }
  .card--back .brand__tagline { left: 130px; top: 220px; font-size: 22px; color: #bfbfbf; letter-spacing: 6px; }
  .license { position: absolute; right: 60px; bottom: 46px; color: #d0d0d0; font-size: 20px; letter-spacing: 1px; }
</style>
</head>
<body>
<main class="sheet">
  <section class="card card--front" aria-label="Business card front">
    <div class="brand">
      <span class="brand__mark"></span>
      <span class="brand__name">corvane</span>
    </div>
    <span class="brand__tagline">home solutions</span>
    <div class="divider"></div>

    <ul class="contacts">
      <li>
        <svg viewBox="0 0 24 24"><path d="M6.6 10.8a15.1 15.1 0 0 0 6.6 6.6l2.2-2.2c.3-.3.7-.4 1-.2 1.1.4 2.3.6 3.6.6.6 0 1 .4 1 1V20c0 .6-.4 1-1 1A17 17 0 0 1 3 4c0-.6.4-1 1-1h3.5c.6 0 1 .4 1 1 0 1.3.2 2.5.6 3.6.1.3 0 .7-.2 1z"/></svg>
        888-316-2790
      </li>
      <li>
        <svg viewBox="0 0 24 24"><path d="M7 1h10a2 2 0 0 1 2 2v18a2 2 0 0 1-2 2H7a2 2 0 0 1-2-2V3a2 2 0 0 1 2-2zm0 4v13h10V5z"/></svg>
        510-742-3185
      </li>
      <li>
        <svg viewBox="0 0 24 24"><path d="M2 4h20v16H2zm2 2v.5l8 5 8-5V6zm0 3v9h16V9l-8 5z"/></svg>
        walter@corvane-hvac.com
      </li>
      <li>
        <svg viewBox="0 0 24 24"><path d="M12 2a10 10 0 1 0 0 20 10 10 0 0 0 0-20zm6.9 6h-3a15 15 0 0 0-1.3-3.9A8 8 0 0 1 18.9 8zM12 4a13 13 0 0 1 1.9 4h-3.8A13 13 0 0 1 12 4zM4.3 14a8 8 0 0 1 0-4h3.4a16 16 0 0 0 0 4zm.8 2h3a15 15 0 0 0 1.3 3.9A8 8 0 0 1 5.1 16zm3-8h-3a8 8 0 0 1 4.3-3.9A15 15 0 0 0 8.1 8zM12 20a13 13 0 0 1-1.9-4h3.8A13 13 0 0 1 12 20zm2.3-6H9.7a14 14 0 0 1 0-4h4.6a14 14 0 0 1 0 4zm.3 5.9a15 15 0 0 0 1.3-3.9h3a8 8 0 0 1-4.3 3.9zm1.7-5.9a16 16 0 0 0 0-4h3.4a8 8 0 0 1 0 4z"/></svg>
        <span>www.<span class="accent">corvane-hvac</span>.com</span>
      </li>
    </ul>

    <div class="person">
      <h1 class="person__name">Walter Brinoku</h1>
      <p class="person__role">Home comfort consultant</p>
      <p class="person__address">4827 Dunmore St<br>#215 Oakland, CA 94619</p>
    </div>
  </section>

  <section class="card card--back" aria-label="Business card back">
    <div class="brand">
      <span class="brand__mark"></span>
      <span class="brand__name">corvane</span>
    </div>
    <span class="brand__tagline">home solutions</span>
    <p class="license">Lic.# 584261</p>
  </section>
</main>
</body>
</html>
```